revised: 'kelvale ironworks' logo -or- business card

we require a business card or a logo that can be used on a business card & other stationery

(i've just recently decided to open this contest up to logo designs as well - but if you have already been working on a card concept, please feel free to continue with it & submit!)

-

We design and build custom brackets and fixings for our customers and their castles, i.e. homes, offices, workshops, farms etc. Our products might be used to:
- brace or support structures, such as houses, decks, small bridges, etc.
- connect any building material to another
- or could simply be a unique piece that exists as a talking point

As part of our design process we would produce drawings/plans/blue prints/prototypes of the product. Our designs factor in multiple elements, from the materials being joined, the client's taste, and the overall durability demanded by the application - if necessary, the bracket may also be endorsed by a third party, such as a stuctural or mechanical engineer.

The build process takes part in our workshop and on the client's site - some elements may be manufactured off-site, depending on the design chosen and the materials used.

Our brackets are designed to our customers' tastes and could be made to be hidden within the structure or exposed to create interest. Our brackets can be large or small, or be neat with clean lines or take on more of an industrial look.
Updates

please note brief has been updated with a more specific description of our business activity

i have also added the final drawing that was used to water-jet the bracket shown in the photos

also, you will note i changed the title to 'logo + business card'

i don't expect a logo as a discrete artefact of the job, however, i expect that some or all elements on the face of the business card will lend themselves to the street sign (as stated in the original brief) as well as any future logo used on letter heads, invoices, etcetera

another update - changed the allowable entries to include logo's only, as well as business cards

Industry/Entity Type

Industrial

Requirements
Must have
• the face should have the name 'Kelvale Ironworks' (or no/all-caps)

the number '75' in the logo, which will also be turned into a conservative (residential) street sign ('75' being a street number) - '75' should stand alone -OR- be readily identified by someone who has previously received a business card

i need to make this '75' and any associated 'framing', so it should be transferrable to cad/dxf for machining, laser/water-cutting, brazing/welding, etcet.

(on that note, the winning designer will be able to share their vision for this sign and we'll adhere to it ... within the realms of possibility! if you're happy with the result then you could include it in your portfolio)
Nice to have
• one side of the card needs a majority of space for quotes, hand-written information, etcet. so this side should be white or a light, complimentary colour suitable for black/blue pen

the following should appear somewhere on the card (there is no email or website) :
- name : Dana Morrow (Proprietor)
- mobile phone number : +61 (0) 498 761203
- abn: 58 904 617 235

any combination of the following (or equivalent) text:

* 'your castle' - this is slang for your house/place (i prefer this to 'home' as 1: it can apply to a place of business, and 2: for me at least, it conjurs images of wrought iron, brass, hardwood & stone)

* unique

* ...

```html
<!DOCTYPE html>
<html lang="en">
<head>
<meta charset="utf-8">
<title>Kelvale Ironworks – Business Card</title>
<link rel="stylesheet" href="https://fonts.googleapis.com/css2?family=Saira+Condensed:wght@600&family=Roboto:wght@400&display=swap">
<style>
  :root {
    --page-bg: #e6e7e8;
    --card-brown: #35230f;
    --accent-orange: #f9a833;
    --mark-brown: #5e4a36;
    --note-paper: #e3dfd9;
    --rule-grey: #a7a19a;
    --contact-text: #d9cfc4;
    --fine-print: #8a7a68;
  }
  * { box-sizing: border-box; margin: 0; padding: 0; }
  html, body {
    width: 1200px;
    height: 900px;
    overflow: hidden;
    background: var(--page-bg);
  }
  .canvas {
    position: relative;
    width: 1200px;
    height: 900px;
  }
  .card {
    position: absolute;
    left: 275px;
    width: 649px;
    height: 360px;
    border-radius: 38px;
    background: var(--card-brown);
    overflow: hidden;
  }
  .card--front { top: 41px; }
  .card--back { top: 473px; }

  /* Front */
  .brand-square {
    position: absolute;
    left: 50%;
    top: 118px;
    width: 56px;
    height: 56px;
    margin-left: -28px;
    background: var(--mark-brown);
  }
  .brand-name {
    position: absolute;
    left: 0;
    right: 0;
    top: 228px;
    text-align: center;
    font-family: "Saira Condensed", "Arial Narrow", sans-serif;
    font-weight: 600;
    font-size: 34px;
    line-height: 1;
    letter-spacing: 0.5px;
    text-transform: uppercase;
    color: var(--accent-orange);
  }

  /* Back */
  .note-panel {
    position: absolute;
    left: 32px;
    top: 33px;
    width: 358px;
    height: 296px;
    border-radius: 12px;
    background: var(--note-paper);
  }
  .note-panel svg { position: absolute; left: 0; top: 0; }
  .note-rule {
    stroke: var(--rule-grey);
    stroke-width: 1;
    stroke-dasharray: 2 2;
  }
  .contact {
    position: absolute;
    left: 405px;
    top: 48px;
    font-family: "Roboto", Arial, sans-serif;
    color: var(--contact-text);
  }
  .contact-name { font-size: 20px; line-height: 24px; }
  .contact-role { font-size: 12px; line-height: 14px; }
  .contact-phones {
    margin-top: 38px;
    font-size: 20px;
    line-height: 28px;
  }
  .abn {
    position: absolute;
    left: 211px;
    top: 334px;
    transform: translateX(-50%);
    font-family: "Roboto", Arial, sans-serif;
    font-size: 11px;
    color: var(--fine-print);
    white-space: nowrap;
  }
</style>
</head>
<body>
<main class="canvas">
  <section class="card card--front">
    <div class="brand-square"></div>
    <h1 class="brand-name">Kelvale Ironworks</h1>
  </section>

  <section class="card card--back">
    <div class="note-panel">
      <svg width="358" height="296" viewBox="0 0 358 296" aria-hidden="true">
        <line class="note-rule" x1="19" x2="339" y1="51.5" y2="51.5"/>
        <line class="note-rule" x1="19" x2="339" y1="89.5" y2="89.5"/>
        <line class="note-rule" x1="19" x2="339" y1="126.5" y2="126.5"/>
        <line class="note-rule" x1="19" x2="339" y1="164.5" y2="164.5"/>
        <line class="note-rule" x1="19" x2="339" y1="202.5" y2="202.5"/>
        <line class="note-rule" x1="19" x2="339" y1="240.5" y2="240.5"/>
        <line class="note-rule" x1="19" x2="339" y1="278.5" y2="278.5"/>
      </svg>
    </div>
    <div class="contact">
      <p class="contact-name">Dana Morrow</p>
      <p class="contact-role">Proprietor</p>
      <p class="contact-phones">0498 761203<br>+61 (0) 498 761203</p>
    </div>
    <p class="abn">abn. 58 904 617 235</p>
  </section>
</main>
</body>
</html>
```